Tovella Fireworks needs a web design and logo

We need a web design and logo for a fireworks business in Sydney Australia, we do public display, weddings, tv, theatrical, clubs and any other organisation that wants to do something special.
Name is Marrowind Fireworks & Pyrotechnics

```html
<!DOCTYPE html>
<html lang="en">
<head>
<meta charset="utf-8">
<title>Marrowind Fireworks &amp; Pyrotechnics</title>
<link rel="stylesheet" href="https://fonts.googleapis.com/css2?family=Open+Sans:ital,wght@0,400;0,600;0,700;1,400&family=Arimo:wght@700&display=swap">
<style>
:root{
  --page:#f5f0f0;
  --header:#dde9f7;
  --brand-blue:#1f55a8;
  --nav-blue:#1d4f9c;
  --ink:#111;
  --body-text:#444;
  --card:#1f1f21;
  --card-text:#e2e2e2;
  --button:#2a5db0;
  --button-dark:#1a4690;
  --footer:#232325;
  --rule:#d9d4d4;
}
*{margin:0;padding:0;box-sizing:border-box}
html,body{width:847px;height:1200px;overflow:hidden}
body{position:relative;background:var(--page);font-family:"Open Sans",Arial,sans-serif;color:var(--body-text)}
.abs{position:absolute}

.site-header{left:0;top:0;width:847px;height:106px;background:var(--header)}
.brand{left:72px;top:39px;font-family:"Arimo",Arial,sans-serif;font-weight:700;font-size:13px;line-height:18px;color:var(--ink);letter-spacing:.2px}
.search{left:632px;top:30px;width:150px;height:19px;border:1px solid #b9c3cf;background:#f4f7fb;font-size:8px;font-style:italic;color:#888;padding:3px 6px}
.search svg{position:absolute;right:6px;top:3px}
.main-nav{top:74px;font-size:8.5px;font-weight:600;color:var(--nav-blue);letter-spacing:.1px}
.main-nav.active{color:var(--ink)}
.main-nav.active::before{content:"";position:absolute;left:0;right:0;top:-6px;height:2px;background:var(--ink)}

.hero{left:0;top:106px;width:847px;height:337px;background:
  radial-gradient(ellipse 150px 120px at 230px 80px,rgba(60,170,170,.55),transparent 70%),
  radial-gradient(ellipse 160px 150px at 500px 140px,rgba(200,90,170,.55),transparent 70%),
  radial-gradient(ellipse 140px 160px at 690px 130px,rgba(230,160,110,.55),transparent 70%),
  radial-gradient(ellipse 120px 90px at 320px 280px,rgba(220,120,90,.45),transparent 70%),
  linear-gradient(180deg,#141c38 0%,#1d2750 60%,#2a2f55 100%)}
.hero-caption{left:76px;top:226px;width:300px;height:92px;background:rgba(20,26,50,.72)}
.hero-title{left:106px;top:250px;font-size:31px;font-weight:700;color:#fff;letter-spacing:.5px}
.hero-arrow{top:260px}
.hero-fade{left:0;top:443px;width:847px;height:28px;background:linear-gradient(180deg,#dde9f7,var(--page))}

.section-title{left:0;width:847px;text-align:center;font-size:18.5px;font-weight:700;color:var(--brand-blue)}
.lead{left:193px;width:464px;text-align:center;font-size:8.6px;line-height:14.5px;color:var(--body-text)}
.btn{display:flex;align-items:center;justify-content:center;background:linear-gradient(180deg,var(--button),var(--button-dark));border:1px solid #174088;color:#fff;font-weight:700}
.btn-primary{left:386px;top:552px;width:75px;height:28px;font-size:9.5px}

.service-name{top:696px;width:228px;text-align:center;font-size:11.5px;font-weight:700;color:var(--brand-blue)}
.service-card{top:724px;width:228px;height:244px;background:var(--card);box-shadow:0 6px 8px -4px rgba(0,0,0,.35)}
.service-photo{position:absolute;left:12px;top:10px;width:204px;height:125px;border-radius:5px}
.photo-wedding{background:linear-gradient(90deg,#111 0%,#2a2a22 35%,#7f8a5a 60%,#e8e6df 80%,#c8cbb8 100%)}
.photo-theatre{background:linear-gradient(180deg,#0b0c3a 0%,#2a1fa0 50%,#3e4bd8 80%,#1b2a8c 100%)}
.photo-club{background:linear-gradient(110deg,#3a0d55 0%,#b42ca8 35%,#2b1840 55%,#4ab07a 75%,#c37ad8 100%)}
.service-text{position:absolute;left:14px;top:150px;width:200px;text-align:center;font-size:8.2px;line-height:14px;color:var(--card-text)}
.service-btn{position:absolute;left:82px;top:201px;width:64px;height:23px;font-size:8.5px}
.carousel-arrow{top:828px}

.divider{left:0;top:1003px;width:847px;height:1px;background:var(--rule)}
.testimonials-title{left:71px;top:1030px;font-size:15px;font-weight:700;color:var(--brand-blue)}
.quote{top:1062px;width:320px;font-size:9px;line-height:14px;font-style:italic;color:#555}
.quote .mark{color:#7fa3d6;font-size:12px;font-style:normal}
.quote-author{top:1118px;font-size:9.5px;font-style:italic;color:var(--brand-blue)}

.site-footer{left:0;top:1166px;width:847px;height:34px;background:var(--footer);border-top:1px solid #000}
.copyright{left:72px;top:11px;font-family:Arial,sans-serif;font-size:8.5px;color:#ddd}
.social{top:12px;width:9px;height:9px;border-radius:50%;background:#ddd}
</style>
</head>
<body>

<header class="abs site-header">
  <div class="abs brand">MARROWIND<br>FIREWORKS &amp; PYROTECHNICS</div>
  <div class="abs search">Search
    <svg width="12" height="12" viewBox="0 0 12 12"><circle cx="5" cy="5" r="3.5" fill="none" stroke="#888" stroke-width="1.4"/><line x1="7.5" y1="7.5" x2="11" y2="11" stroke="#888" stroke-width="2"/></svg>
  </div>
  <nav>
    <span class="abs main-nav active" style="left:439px">HOME</span>
    <span class="abs main-nav" style="left:502px">ABOUT US</span>
    <span class="abs main-nav" style="left:579px">SERVICES</span>
    <span class="abs main-nav" style="left:652px">PRODUCT</span>
    <span class="abs main-nav" style="left:729px">CONTACT US</span>
  </nav>
</header>

<section class="abs hero" role="img" aria-label="Night sky filled with colourful firework bursts"></section>
<div class="abs hero-caption"></div>
<div class="abs hero-title">GOOD QUALITY</div>
<svg class="abs hero-arrow" style="left:24px" width="20" height="20" viewBox="0 0 20 20"><path d="M17 10H4M9 5L4 10l5 5" fill="none" stroke="rgba(255,255,255,.35)" stroke-width="2.5"/></svg>
<svg class="abs hero-arrow" style="left:800px" width="20" height="20" viewBox="0 0 20 20"><path d="M3 10h13M11 5l5 5-5 5" fill="none" stroke="rgba(255,255,255,.35)" stroke-width="2.5"/></svg>
<div class="abs hero-fade"></div>

<h1 class="abs section-title" style="top:467px">WELCOME TO OUR SITE</h1>
<p class="abs lead" style="top:503px">Lorem Ipsum has been the industry's standard dummy text ever since the 1500s, when an unknown printer took a galley of type and scrambled it to make a type specimen remaining essentially unchanged</p>
<div class="abs btn btn-primary">READ MORE</div>

<h2 class="abs section-title" style="top:613px">OUR SERVICES</h2>
<p class="abs lead" style="top:650px">Lorem Ipsum has been the industry's standard dummy text ever since the 1500s, when an unknown printer took a galley of type and scrambled it to make a type specimen remaining essentially unchanged</p>

<h3 class="abs service-name" style="left:75px">WEDDINGS</h3>
<h3 class="abs service-name" style="left:315px">THEATRICAL</h3>
<h3 class="abs service-name" style="left:554px">CLUBS</h3>

<article class="abs service-card" style="left:73px">
  <div class="service-photo photo-wedding" role="img" aria-label="Bride and groom holding hands outdoors"></div>
  <p class="service-text">Contrary to popular belief, Lorem Ipsum is not simply random text. It has roots in orem Ipsum is not simply random text. It</p>
  <div class="btn service-btn">READ MORE</div>
</article>
<article class="abs service-card" style="left:314px">
  <div class="service-photo photo-theatre" role="img" aria-label="Empty stage lit with blue lights"></div>
  <p class="service-text">Contrary to popular belief, Lorem Ipsum is not simply random text. It has roots inorem Ipsum is not simply random text. It</p>
  <div class="btn service-btn">READ MORE</div>
</article>
<article class="abs service-card" style="left:554px">
  <div class="service-photo photo-club" role="img" aria-label="Nightclub interior with pink and green lighting"></div>
  <p class="service-text">Contrary to popular belief, Lorem Ipsum is not simply random text. It has roots inorem Ipsum is not simply random text. It</p>
  <div class="btn service-btn">READ MORE</div>
</article>

<svg class="abs carousel-arrow" style="left:28px" width="14" height="22" viewBox="0 0 14 22"><path d="M11 2L3 11l8 9" fill="none" stroke="#aaa" stroke-width="2"/></svg>
<svg class="abs carousel-arrow" style="left:804px" width="14" height="22" viewBox="0 0 14 22"><path d="M3 2l8 9-8 9" fill="none" stroke="#aaa" stroke-width="2"/></svg>

<div class="abs divider"></div>
<h2 class="abs testimonials-title">TESTIMONIALS</h2>
<blockquote class="abs quote" style="left:70px"><span class="mark">“</span>There are many variations of passages of Lorem Ipsum available, but the majority have suffered alteration in some form, by injected humour, or randomised words which don't look even slightly believable. <span class="mark">”</span></blockquote>
<blockquote class="abs quote" style="left:415px"><span class="mark">“</span>There are many variations of passages of Lorem Ipsum available, but the majority have suffered alteration in some form, by injected humour, or randomised words which don't look even slightly believable.<span class="mark">”</span></blockquote>
<div class="abs quote-author" style="left:362px">-lena harwick-</div>
<div class="abs quote-author" style="left:704px">-owen callery-</div>

<footer class="abs site-footer">
  <div class="abs copyright">©2015.MARROWIND FIREWORKS &amp; PYROTECHNICS</div>
  <span class="abs social" style="left:710px"></span>
  <span class="abs social" style="left:729px"></span>
  <span class="abs social" style="left:748px"></span>
  <span class="abs social" style="left:767px"></span>
</footer>

</body>
</html>
```